New design for www.TrimTable.com

On TrimTable you can find & book your hairdresser. TrimTable is the biggest platform in the Netherlands.

- The design should be a responcive design
- Should be able to go global, should fit in perfectly between all the big booking platforms like stayvo, ridlo etc,
- Should have te result of more bookings. :)
- We are ‘only’ asking a beautiful design, not a technical solution.
- We need a homepage (https://trimtable.com/), search resultpage ((https://trimtable.com/kapper/amsterdam/#), salonpage (https://trimtable.com/kapper/vorden/lumo-for-hair/), about us page (https://trimtable.com/aboutus/), for the hairdresser info page (https://trimtable.com/kapper/), login/register page (https://trimtable.com/account/signin/).

- On the page of the hairdresser there is a dynamic part. The part where you create your appointment. Please take a look at this part too after you choose your treatment (behandeling), employee (medewerker), Date (datum) and time (tijd). The part that you see after this, is the part where you fill in your data as a consumer.

I've added more logo's but mostly we use the green color.

A few of our competitors: www.plumsalo.com, www.korifex.com

Target Market(s)

All consumers

Industry/Entity Type

Hair And Beauty

Number of Pages Required

5+ page

Font styles to use
Sans Serif

Colors
abd036
c3c3c3
757575

Requirements
Must have
• Responsive
• We did an A/B test with the homepage. It turns out that option B works better then option A (take a look at the uploaded pictures). So what we need on the homepage: The USP's with the green checkboxes, The search button needs to by dynamic (changes for example from light green to dark green so you can see you can click it) The call to action sentence Zoek & Vind je kapsalon, the searchfield and searchbutton should be seperated.
Nice to have
• The style that we like is the flat design style. The website should be simple, clean and it should feel a bit like a luxury thing. Because an appointment with the hairdresser can be a real treat and luxury moment for yourself.
• The luxury feeling and flat design that is in the www.ridlo.com website is really nice for example. But then it has to be a bit more light and not so black and dark.

```html
<!DOCTYPE html>
<html lang="en">
<head>
<meta charset="utf-8">
<title>TrimTable – Find &amp; book your hairdresser</title>
<link rel="stylesheet" href="https://fonts.googleapis.com/css2?family=Raleway:wght@300;400;600;700&family=Open+Sans:wght@400;600;700&display=swap">
<style>
  :root{
    --green:#8cc63e;
    --green-dark:#6fa82a;
    --orange:#f26b21;
    --ink:#3a3a3a;
    --grey:#757575;
    --grey-light:#c3c3c3;
    --panel:#f1f1f1;
    --footer:#f6f6f6;
    --dark:#3d3d3d;
    --white:#ffffff;
  }
  *{box-sizing:border-box;margin:0;padding:0}
  html,body{width:1200px;height:2200px;overflow:hidden;background:var(--white)}
  body{font-family:"Open Sans",Arial,sans-serif;color:var(--ink);position:relative}
  h1,h2,h3,h4{font-family:"Raleway",Arial,sans-serif}

  /* Hero */
  .hero{position:absolute;left:0;top:0;width:1200px;height:540px;overflow:hidden}
  .hero__photo{position:absolute;inset:0;background:
    radial-gradient(ellipse at 70% 40%,#b98a6e 0%,#7a5444 30%,transparent 60%),
    linear-gradient(100deg,#5b4038 0%,#8e6a5a 35%,#6d4a40 60%,#3a2b28 100%)}
  .hero__shade{position:absolute;inset:0;background:rgba(40,25,22,.35)}
  .brand{position:absolute;left:40px;top:34px;display:flex;align-items:center;gap:12px;color:var(--white);font-family:"Raleway",Arial,sans-serif;font-weight:600;font-size:30px}
  .brand__dot{width:40px;height:40px;border-radius:50%;background:var(--white)}
  .account{position:absolute;right:196px;top:46px;display:flex;gap:10px}
  .account a{display:block;border:1px solid rgba(255,255,255,.8);color:var(--white);font-size:12px;font-weight:600;letter-spacing:.5px;padding:6px 12px;text-decoration:none}
  .hero__title{position:absolute;left:0;right:0;top:196px;text-align:center;color:var(--white)}
  .hero__title .lead{display:block;font-weight:400;font-size:32px}
  .hero__title .big{display:block;font-weight:400;font-size:48px;margin-top:6px}
  .search{position:absolute;left:228px;top:306px;display:flex;gap:10px}
  .search__field{width:512px;height:44px;background:var(--white);border:0;padding:0 18px;font-size:14px;color:#9a9a9a;display:flex;align-items:center}
  .search__button{width:120px;height:44px;background:var(--green);color:var(--white);font-size:16px;font-weight:600;display:flex;align-items:center;justify-content:center}
  .slider-dots{position:absolute;left:0;right:0;top:500px;display:flex;justify-content:center;gap:8px}
  .slider-dots span{width:14px;height:14px;border-radius:50%;background:rgba(255,255,255,.55)}
  .slider-dots span.is-active{background:var(--white)}

  /* Stats */
  .stats{position:absolute;left:0;top:540px;width:1200px;height:290px;display:flex;justify-content:center;gap:30px;padding-top:54px}
  .stat{width:150px;text-align:center}
  .stat__circle{width:150px;height:150px;border-radius:50%;position:relative;overflow:hidden;background:linear-gradient(135deg,#8b6a58,#3f2f2a)}
  .stat__circle::after{content:"";position:absolute;inset:0;background:rgba(0,0,0,.3)}
  .stat__num{position:absolute;inset:0;display:flex;align-items:center;justify-content:center;z-index:1;color:var(--white);font-family:"Raleway",Arial,sans-serif;font-size:30px;font-weight:600}
  .stat__label{margin-top:14px;font-size:15px;color:var(--ink);line-height:1.3}

  /* App */
  .app{position:absolute;left:0;top:840px;width:1200px;height:360px;background:var(--panel)}
  .app__copy{position:absolute;left:172px;top:76px;width:500px}
  .app__copy h2{font-size:34px;font-weight:400;line-height:1.2;color:var(--ink)}
  .app__copy .strong{margin-top:14px;font-size:12px;font-weight:700;color:var(--ink)}
  .app__copy p{margin-top:6px;font-size:11px;line-height:1.65;color:var(--grey)}
  .btn-download{display:inline-block;margin-top:18px;background:var(--orange);color:var(--white);font-size:14px;font-weight:600;padding:10px 20px}
  .app__visual{position:absolute;left:760px;top:10px;width:230px;height:350px;border-radius:8px;background:linear-gradient(160deg,#e8e4e0,#cfc6bd)}

  /* How it works */
  .how{position:absolute;left:0;top:1200px;width:1200px;height:430px}
  .how__tag{position:absolute;left:528px;top:70px;width:144px;height:34px;border:1px solid var(--grey-light);border-radius:17px;background:var(--white);display:flex;align-items:center;justify-content:center;font-size:14px;color:var(--grey)}
  .how__line{position:absolute;left:0;top:0}
  .step{position:absolute;top:130px;width:240px;text-align:center}
  .step svg{display:block;margin:0 auto}
  .step h3{margin-top:14px;font-family:"Open Sans",Arial,sans-serif;font-size:15px;font-weight:600;color:var(--ink)}
  .step p{margin-top:6px;font-size:11px;line-height:1.5;color:var(--grey)}

  /* Newsletter */
  .news{position:absolute;left:0;top:1632px;width:1200px;height:248px;background:linear-gradient(90deg,#3b3b3b,#4d4d4d 50%,#3a3a3a)}
  .news h2{position:absolute;left:0;right:0;top:46px;text-align:center;color:var(--white);font-size:30px;font-weight:400}
  .news p{position:absolute;left:0;right:0;top:92px;text-align:center;color:#d6d6d6;font-size:13px}
  .news__form{position:absolute;left:410px;top:144px;display:flex}
  .news__field{width:290px;height:38px;background:var(--white);display:flex;align-items:center;padding:0 14px;font-size:12px;color:#9a9a9a}
  .news__button{width:110px;height:38px;background:var(--orange);color:var(--white);font-size:13px;font-weight:600;display:flex;align-items:center;justify-content:center}

  /* Footer */
  .footer{position:absolute;left:0;top:1880px;width:1200px;height:320px;background:var(--footer)}
  .footer__col{position:absolute;top:66px}
  .footer__col h4{font-family:"Open Sans",Arial,sans-serif;font-size:15px;font-weight:600;color:var(--ink);margin-bottom:10px}
  .footer__col li{list-style:none;font-size:11px;color:var(--grey);line-height:1.9}
  .social{display:flex;gap:10px;margin-top:8px}
  .social span{width:18px;height:18px;border-radius:50%;background:var(--dark)}
  .footer__legal{position:absolute;left:180px;top:278px;font-size:10px;color:var(--grey)}
  .footer__top{position:absolute;right:180px;top:274px;width:22px;height:22px;background:var(--grey-light)}
</style>
</head>
<body>

<header class="hero">
  <div class="hero__photo" role="img" aria-label="Photo of a smiling man at a barbershop"></div>
  <div class="hero__shade"></div>
  <div class="brand"><span class="brand__dot"></span>TrimTable</div>
  <nav class="account"><a href="#">LOG IN</a><a href="#">SIGN UP</a></nav>
  <h1 class="hero__title">
    <span class="lead">The greatest hairdresser booking site in the</span>
    <span class="big">Netherlands with 541 hairdressers</span>
  </h1>
  <div class="search">
    <div class="search__field">Enter city or name of salon</div>
    <div class="search__button">Search</div>
  </div>
  <div class="slider-dots"><span class="is-active"></span><span></span><span></span><span></span></div>
</header>

<section class="stats">
  <div class="stat"><div class="stat__circle" role="img" aria-label="Salon interior photo"><span class="stat__num">541</span></div><div class="stat__label">Salons</div></div>
  <div class="stat"><div class="stat__circle" role="img" aria-label="Hair treatment photo"><span class="stat__num">16,413</span></div><div class="stat__label">Treatments for<br>booking</div></div>
  <div class="stat"><div class="stat__circle" role="img" aria-label="Appointment photo"><span class="stat__num">5,20,827</span></div><div class="stat__label">Agreements</div></div>
  <div class="stat"><div class="stat__circle" role="img" aria-label="Hairdresser at work photo"><span class="stat__num">7,180</span></div><div class="stat__label">Hairdressers booking</div></div>
  <div class="stat"><div class="stat__circle" role="img" aria-label="Happy customer photo"><span class="stat__num">26,629</span></div><div class="stat__label">Reliable reviews</div></div>
</section>

<section class="app">
  <div class="app__copy">
    <h2>All the hairdressers of<br>Netherlands in your pocket?</h2>
    <div class="strong">Find all hairdressers in one place, book in seconds, pay at the salon.</div>
    <p>Browse salons near you, compare prices and reviews, and choose the stylist and time that suits your day. Our app keeps every booking in your pocket and reminds you before each visit.</p>
    <span class="btn-download">Download Now</span>
  </div>
  <div class="app__visual" role="img" aria-label="Hand holding a smartphone showing the booking app"></div>
</section>

<section class="how">
  <svg class="how__line" width="1200" height="430" viewBox="0 0 1200 430">
    <path d="M360 210 C 420 140, 520 140, 560 200" fill="none" stroke="#c3c3c3" stroke-width="2" stroke-dasharray="6 6"/>
    <path d="M640 200 C 690 140, 780 140, 840 210" fill="none" stroke="#c3c3c3" stroke-width="2" stroke-dasharray="6 6"/>
    <line x1="672" y1="87" x2="1000" y2="87" stroke="#e0e0e0"/>
    <line x1="200" y1="87" x2="528" y2="87" stroke="#e0e0e0"/>
  </svg>
  <div class="how__tag">How It Works</div>

  <div class="step" style="left:200px">
    <svg width="110" height="150" viewBox="0 0 110 150">
      <path d="M55 148 C 40 110, 4 88, 4 54 A51 51 0 0 1 106 54 C106 88, 70 110, 55 148 Z" fill="var(--green)"/>
      <g fill="#fff">
        <rect x="32" y="42" width="18" height="28" rx="6"/><rect x="60" y="42" width="18" height="28" rx="6"/>
        <rect x="48" y="46" width="14" height="10"/><rect x="35" y="32" width="12" height="12" rx="2"/><rect x="63" y="32" width="12" height="12" rx="2"/>
      </g>
    </svg>
    <h3>Search &amp; Find hairdresser</h3>
    <p>Search salons near you and compare<br>their ratings and prices.</p>
  </div>

  <div class="step" style="left:480px">
    <svg width="110" height="150" viewBox="0 0 110 150">
      <path d="M55 148 C 40 110, 4 88, 4 54 A51 51 0 0 1 106 54 C106 88, 70 110, 55 148 Z" fill="var(--green)"/>
      <rect x="32" y="34" width="46" height="40" rx="3" fill="#fff"/>
      <rect x="32" y="34" width="46" height="9" fill="#e8f3d6"/>
      <g fill="var(--green)"><rect x="37" y="48" width="7" height="6"/><rect x="48" y="48" width="7" height="6"/><rect x="59" y="48" width="7" height="6"/><rect x="70" y="48" width="5" height="6"/><rect x="37" y="60" width="7" height="6"/><rect x="48" y="60" width="7" height="6"/><rect x="59" y="60" width="7" height="6"/></g>
      <rect x="40" y="28" width="4" height="10" fill="#fff"/><rect x="66" y="28" width="4" height="10" fill="#fff"/>
    </svg>
    <h3>Book your Appointment</h3>
    <p>Pick a treatment, stylist and time,<br>then confirm in one click.</p>
  </div>

  <div class="step" style="left:760px">
    <svg width="110" height="150" viewBox="0 0 110 150">
      <path d="M55 148 C 40 110, 4 88, 4 54 A51 51 0 0 1 106 54 C106 88, 70 110, 55 148 Z" fill="var(--green)"/>
      <path d="M55 28 L61 47 L81 47 L65 59 L71 78 L55 66 L39 78 L45 59 L29 47 L49 47 Z" fill="#fff"/>
    </svg>
    <h3>Enjoy your new hairstyle</h3>
    <p>Relax at the salon and leave<br>with a fresh new look.</p>
  </div>
</section>

<section class="news" role="img" aria-label="Dimmed salon photo behind the newsletter signup">
  <h2>Nice TrimTable get tips? Subscribe!</h2>
  <p>Receive tips, trends and exclusive offers straight to your inbox.</p>
  <div class="news__form">
    <div class="news__field">Email address</div>
    <div class="news__button">Subscribe</div>
  </div>
</section>

<footer class="footer">
  <div class="footer__col" style="left:180px"><h4>Quick links</h4><ul><li>About us</li><li>How it works</li><li>Blog</li><li>Contact</li></ul></div>
  <div class="footer__col" style="left:360px"><h4>Sublinks</h4><ul><li>Barber Utrecht</li><li>Barber Eindhoven</li><li>Barber Tilburg</li></ul></div>
  <div class="footer__col" style="left:520px"><h4>Resources</h4><ul><li>Barber Groningen</li><li>Barber Haarlem</li><li>Barber Arnhem</li></ul></div>
  <div class="footer__col" style="left:672px"><h4>Locations</h4><ul><li>Barber Breda</li><li>Barber Nijmegen</li><li>Barber Leiden</li></ul></div>
  <div class="footer__col" style="left:832px"><h4>Follow us</h4><ul><li>Please connect with us</li></ul><div class="social"><span></span><span></span><span></span><span></span></div></div>
  <div class="footer__legal">© 2024 TrimTable. All rights reserved. Terms of use.</div>
  <div class="footer__top"></div>
</footer>

</body>
</html>
```